Teeth Whitening Clinic Website Redesign - Social Proof Theme

NEW TEETH SITEREVAMP CURRENT WEBSITE:WWW.SANDIEGOSTEETHWHITENING.COMTHEME:SOCIAL PROOF/5 STAR REVIEWS/TESTIMONIALS THEME:https://maps.example.net/QxRvPLoKzN84 I want a testimonial themed, social proof themed website so customers will be sold by testimonials all over the website….I like a nice clean simple site but with all important factors standing out like CALLS TO ACTIONS, for example the $99 special link in header on original design. Also, testimonials throughout the website placed methodically as not to be FORCED and CLUTTEREDKeep all same exact content for all pages and elements of current design. All buttons, calls to action, navigation, etc. Please do not leave anything out from current design. SPECIAL INSTRUCTIONS for banner image:I want to use actual customer photos inside the banner image in a way that really pops and grabs attention. Please grab some customer photos from my PG Account, fk or rateway account: Also, I want to integrate 5 star rateway logo, friendbook review 5 stars icon, searchly business page 5 stars icon, etc. on the banner as well to show social proof as much as possible. Actual customer photos to be used throughout website:https://www.photogram.example/brightharborsmilestudioplace/ https://www.friendbook.com/SDTeethWhitening/https://www.reviewhub.example/biz/bright-harbor-smile-studio-place-bright-harbor-5 Reviews:https://www.reviewhub.example/biz/bright-harbor-smile-studio-place-bright-harbor-5 https://www.friendbook.com/pg/SDTeethWhitening/reviews/?ref=page_internalhttps://goo.gl/maps/TmJcABLAJwC2 Please do home page first to come up with theme then after approval home page we can move forward additional pages.

Target Market(s)

PEOPLE THAT CARE ABOUT DENTAL HYGEINE AND OR CARE ABOUT THEIR TEETH SMILE

Industry/Entity Type

Dental Clinic

Number of Pages Required

5+ page

Colors

Designer to choose colors to be used in the design.

Requirements
Must have
• NEW TEETH SITE
• REVAMP CURRENT WEBSITE:
• WWW.BRIGHTHARBORSMILESTUDIO.EXAMPLE
• THEME:
• SOCIAL PROOF/5 STAR REVIEWS/TESTIMONIALS THEME:
• https://maps.example.net/QxRvPLoKzN84
• I want a testimonial themed, social proof themed website so customers will be sold by testimonials all over the website….I like a nice clean simple site but with all important factors standing out like CALLS TO ACTIONS, for example the $99 special link in header on original design. Also, testimonials throughout the website placed methodically as not to be FORCED and CLUTTERED
• Keep all same exact content for all pages and elements of current design. All buttons, calls to action, navigation, etc. Please do not leave anything out from current design.
• SPECIAL INSTRUCTIONS for banner image:
• I want to use actual customer photos inside the banner image in a way that really pops and grabs attention. Please grab some customer photos from my PG Account, fk or rateway account:
• Also, I want to integrate 5 star rateway logo, friendbook review 5 stars icon, searchly business page 5 stars icon, etc. on the banner as well to show social proof as much as possible.
• Actual customer photos to be used throughout website:
• https://www.photogram.example/brightharborsmilestudioplace/
• https://www.friendbook.example/BHSmileStudio/
• https://www.reviewhub.example/biz/bright-harbor-smile-studio-place-bright-harbor-5
• Reviews:
• https://www.friendbook.example/pg/BHSmileStudio/reviews/?ref=page_internal
• Please do home page first to come up with theme then after approval home page we can move forward additional pages.
Nice to have
• NEW TEETH SITE
• REVAMP CURRENT WEBSITE:
• THEME:
• Reviews:
Should not have
• NEW TEETH SITE
• REVAMP CURRENT WEBSITE:
• THEME:
• Reviews:

```html
<!DOCTYPE html>
<html lang="en">
<head>
<meta charset="utf-8">
<title>Bright Harbor Smile Studio</title>
<link rel="stylesheet" href="https://fonts.googleapis.com/css2?family=Cinzel:wght@400;700&family=Montserrat:wght@400;500;600;700;800&display=swap">
<style>
:root{
  --blue:#1fa9d6;
  --blue-deep:#1588b5;
  --blue-light:#5cc6ea;
  --navy:#0f3550;
  --ink:#333;
  --muted:#777;
  --line:#e2e2e2;
  --gray-bg:#efefef;
  --white:#fff;
  --star:#e8323c;
  --gold:#f4b400;
}
*{box-sizing:border-box;margin:0;padding:0}
html,body{width:1200px;height:4604px;overflow:hidden}
body{font-family:"Montserrat",sans-serif;color:var(--ink);background:var(--white);position:relative}
.abs{position:absolute}
.serif{font-family:"Cinzel",serif}
.center{text-align:center;left:0;right:0}

/* top bar */
.topbar{top:0;left:0;width:1200px;height:40px;background:#f3f3f3;border-bottom:1px solid var(--line);font-size:13px;color:#555}
.topbar .hours{left:80px;top:12px;display:flex;gap:8px;align-items:center}
.topbar .contact{right:80px;top:11px;display:flex;gap:18px;align-items:center}
.dot{width:12px;height:12px;border-radius:50%;background:var(--blue);display:inline-block}
.soc{width:14px;height:14px;border-radius:3px;background:#9aa7ad;display:inline-block}

/* header */
.header{top:40px;left:0;width:1200px;height:98px;background:var(--white)}
.deal{left:80px;top:24px;display:flex;align-items:center;gap:14px;font-size:13px;font-weight:700;color:var(--ink);line-height:18px}
.deal .badge{width:46px;height:46px;background:var(--blue);border-radius:4px}
.deal small{font-weight:400;color:var(--muted)}
.brand{left:480px;top:16px;width:240px;display:flex;align-items:center;gap:12px}
.brand .mark{width:58px;height:58px;border-radius:50%;border:2px solid #c9d4d9}
.brand .name{font-family:"Cinzel",serif;font-weight:700;color:var(--blue-deep);font-size:19px;line-height:22px}
.btn{display:inline-flex;align-items:center;justify-content:center;background:var(--blue);color:var(--white);font-size:14px;font-weight:600;letter-spacing:.5px;text-transform:uppercase;border-radius:3px}
.btn .arrow{width:24px;align-self:stretch;background:rgba(255,255,255,.25);display:flex;align-items:center;justify-content:center;margin-left:14px}
.btn-book{right:80px;top:26px;height:50px;width:262px;padding-left:20px}
.btn-grey{background:#8f9aa0}

/* nav */
.nav{top:138px;left:0;width:1200px;height:57px;background:linear-gradient(90deg,var(--blue),var(--blue-light));}
.nav ul{list-style:none;display:flex;position:absolute;left:78px;top:0;height:57px}
.nav li{color:var(--white);font-size:13px;font-weight:600;padding:0 14px;line-height:57px;text-transform:uppercase}
.nav li.active{background:#9aa3a8}

/* hero */
.hero{top:195px;left:0;width:1200px;height:520px;background:linear-gradient(100deg,#dff3fb 0%,#8fd8f0 30%,#31b3de 60%,var(--blue) 100%);overflow:hidden}
.hero-photo{left:0;top:0;width:600px;height:470px;background:radial-gradient(ellipse at 40% 60%,rgba(255,255,255,.6),rgba(255,255,255,0) 70%)}
.hero h1{left:78px;top:125px;font-size:35px;font-weight:800;color:var(--navy);line-height:42px;text-transform:uppercase}
.hero .lead{left:78px;top:220px;width:420px;font-size:14px;color:var(--navy);line-height:20px}
.hero .ctas{left:78px;top:290px;display:flex;gap:20px}
.hero .ctas .btn{height:48px;width:240px;padding-left:20px;position:static}
.reviews-row{left:78px;top:365px;display:flex;gap:22px;align-items:flex-end}
.review-mark{display:flex;flex-direction:column;gap:3px}
.review-mark .word{font-size:20px;font-weight:700;color:var(--navy)}
.stars{display:flex;gap:3px}
.stars i{width:12px;height:12px;background:var(--gold);clip-path:polygon(50% 0,61% 35%,98% 35%,68% 57%,79% 91%,50% 70%,21% 91%,32% 57%,2% 35%,39% 35%)}
.stars.red i{background:var(--star)}
.collage{left:600px;top:0;width:600px;height:460px;display:grid;grid-template-columns:repeat(4,1fr);grid-template-rows:repeat(3,1fr);gap:8px;padding:8px}
.collage div{background:linear-gradient(160deg,#c9a48d,#6f8fa3 60%,#3a9cc8);border-radius:2px;opacity:.9}
.collage div:nth-child(3n){background:linear-gradient(160deg,#8fc7de,#b08a74 60%,#5aa9d1)}
.collage div:nth-child(4n+1){opacity:.55}
.wave{left:0;bottom:0;width:1200px;height:90px}

/* intro */
.intro{top:715px;left:0;width:1200px;height:620px}
.intro .mark{left:560px;top:45px;width:80px;height:80px;border-radius:50%;border:2px solid #cdd6da}
.intro h2{top:130px;font-size:37px;font-weight:400;color:var(--navy)}
.intro .tag{top:182px;font-size:20px;font-weight:700;color:var(--blue-deep)}
.intro p{left:300px;width:600px;top:230px;font-size:13px;line-height:22px;color:var(--muted);text-align:center}
.video{left:390px;top:372px;width:510px;height:340px;background:linear-gradient(180deg,#2a2f33,#5a6a72 50%,#262a2d);color:var(--white);z-index:2}
.video .title{left:20px;top:16px;font-size:14px}
.video .play{left:215px;top:130px;width:80px;height:56px;border-radius:12px;background:rgba(0,0,0,.6)}
.video .play:after{content:"";position:absolute;left:31px;top:16px;border-left:22px solid var(--white);border-top:12px solid transparent;border-bottom:12px solid transparent}
.video .bar{left:20px;right:20px;bottom:18px;height:4px;background:rgba(255,255,255,.35)}
.video .time{left:20px;bottom:30px;font-size:12px}

/* how it works */
.how{top:1335px;left:0;width:1200px;height:860px;background:linear-gradient(180deg,var(--blue),#21a4d0);color:var(--white)}
.how h2{top:162px;font-size:40px;font-weight:400}
.how p{left:170px;width:860px;font-size:13px;line-height:22px;text-align:center}
.how .p1{top:222px}
.how .p2{top:552px}
.steps{left:77px;top:353px;width:1045px;display:flex;justify-content:space-between}
.steps div{width:152px;height:154px;background:linear-gradient(160deg,#d9d2cc,#7a8a94 60%,#30444f)}
.steps div:nth-child(5){background:linear-gradient(160deg,#4b57b0,#b8b2ec 60%,#2b2f5a)}
.how .btn{left:470px;top:752px;width:260px;height:46px;background:#a4adb2;padding-left:20px}

/* why */
.why{top:2195px;left:0;width:1200px;height:620px}
.why h2{top:70px;font-size:40px;font-weight:400;color:var(--ink)}
.why .photo{left:60px;top:138px;width:510px;height:475px;background:linear-gradient(180deg,#e9eef0,#b58a70 55%,#6a7f86)}
.benefit{width:180px;text-align:center}
.benefit .ring{width:116px;height:116px;margin:0 auto;border-radius:50%;border:4px solid var(--blue);display:flex;align-items:center;justify-content:center;box-shadow:0 4px 10px rgba(0,0,0,.1)}
.benefit span{display:block;margin-top:10px;font-family:"Cinzel",serif;font-size:15px;font-weight:700;letter-spacing:.5px}

/* compare */
.compare{top:2815px;left:0;width:1200px;height:585px;background:linear-gradient(180deg,#f6f6f6,var(--gray-bg))}
.compare h2{top:58px;font-size:38px;font-weight:700;color:var(--ink)}
.table{left:77px;top:147px;width:1043px;display:flex}
.col{width:209px;background:var(--white);border-right:1px solid var(--line);height:383px;box-shadow:0 2px 6px rgba(0,0,0,.08)}
.col .head{height:100px;background:linear-gradient(180deg,#dcdcdc,#c8c8c8);display:flex;align-items:center;justify-content:center;font-family:"Cinzel",serif;font-weight:700;font-size:17px;color:var(--white);letter-spacing:1px}
.col ul{list-style:none;padding:18px 34px}
.col li{font-size:13px;height:42px;line-height:42px;border-bottom:1px solid #eee;color:#444}
.col.feature{background:var(--blue);margin-top:-10px;height:420px;border:none;z-index:2}
.col.feature .head{background:var(--white);margin:6px;height:98px;color:var(--blue-deep);font-size:16px;flex-direction:column;line-height:20px}
.col.feature li{color:var(--white);border-color:rgba(255,255,255,.3)}

/* testimonials */
.testi{top:3400px;left:0;width:1200px;height:710px}
.testi h2{top:70px;font-size:38px;font-weight:400;color:var(--ink)}
.card{left:184px;top:138px;width:844px;height:385px;background:var(--white);box-shadow:0 3px 14px rgba(0,0,0,.12)}
.avatar{left:377px;top:-20px;width:90px;height:90px;border-radius:50%;background:linear-gradient(135deg,#f2c94c,#d96b6b);border:4px solid var(--white);box-shadow:0 2px 6px rgba(0,0,0,.2)}
.card .rating{left:0;right:0;top:125px;display:flex;justify-content:center;gap:4px}
.card .rating i{width:24px;height:24px;background:var(--star);position:relative}
.card .rating i:after{content:"";position:absolute;inset:5px;background:var(--white);clip-path:polygon(50% 0,61% 35%,98% 35%,68% 57%,79% 91%,50% 70%,21% 91%,32% 57%,2% 35%,39% 35%)}
.card p{left:90px;width:664px;top:170px;font-size:13px;line-height:22px;text-align:center;color:#555}
.card .who{top:285px;font-family:"Cinzel",serif;font-size:18px;line-height:30px}
.chev{top:340px;width:18px;height:18px;border-top:2px solid #bbb;border-right:2px solid #bbb}
.logos{top:590px;display:flex;justify-content:center;gap:50px;align-items:flex-end}

/* footer */
.footer{top:4110px;left:0;width:1200px;height:494px;background:linear-gradient(180deg,#2fb4e0,var(--blue));color:var(--white);text-align:center}
.footer .mark{left:545px;top:35px;width:110px;height:110px;border-radius:50%;border:3px solid rgba(255,255,255,.8)}
.footer .addr{top:208px;font-size:14px;display:flex;justify-content:center;gap:50px;align-items:center}
.footer .links{left:110px;width:980px;font-size:13px;line-height:30px;top:276px}
.footer .social{top:385px;display:flex;justify-content:center;gap:6px}
.footer .social span{width:28px;height:28px;background:rgba(255,255,255,.3);border-radius:3px}
.footer .copy{top:440px;font-size:12px;opacity:.9}
</style>
</head>
<body>

<div class="abs topbar">
  <div class="abs hours"><span class="dot"></span>Clinic Open: Mon-Fri 9:15 am to 5:30 pm Sat 10am to 2pm</div>
  <div class="abs contact"><span><span class="dot"></span> 1-555-014-2280</span><span class="soc"></span><span class="soc"></span><span class="soc"></span></div>
</div>

<header class="abs header">
  <div class="abs deal"><span class="badge"></span><div>Click Here to Get Our <span style="color:var(--blue)">$99</span> Teeth<br>Whitening Deal <small>(Reg. $379)</small></div></div>
  <div class="abs brand"><span class="mark"></span><span class="name">Bright Harbor<br>Smile Studio</span></div>
  <a class="abs btn btn-book">Book Appointment<span class="arrow">›</span></a>
</header>

<nav class="abs nav">
  <ul>
    <li class="active">Home</li><li>Our Process</li><li>Photos</li><li>Free Treatments</li><li>Testimonials</li><li>Blog</li><li>FAQ</li><li>Contact</li><li>Gift Certificates</li>
  </ul>
</nav>

<section class="abs hero">
  <div class="abs hero-photo" role="img" aria-label="Close-up of a bright white smile"></div>
  <h1 class="abs">Get That White Smile<br>You've Always Wanted</h1>
  <p class="abs lead">Amazing Results. The Most Effective System, More Affordable Than The Dentist</p>
  <div class="abs ctas">
    <a class="btn">Book Online<span class="arrow">›</span></a>
    <a class="btn btn-grey">Contact Us<span class="arrow">›</span></a>
  </div>
  <div class="abs reviews-row">
    <div class="review-mark"><span class="word">friendbook</span><span class="stars"><i></i><i></i><i></i><i></i><i></i></span></div>
    <div class="review-mark"><span class="word">searchly</span><span style="font-size:11px;color:var(--navy)">Reviews ★★★★★</span></div>
    <div class="review-mark"><span class="word">rateway</span><span class="stars red"><i></i><i></i><i></i><i></i><i></i></span></div>
    <div class="review-mark"><span class="word">searchly</span><span style="font-size:11px;color:var(--navy)">My Business</span></div>
  </div>
  <div class="abs collage" role="img" aria-label="Collage of happy customer photos">
    <div></div><div></div><div></div><div></div><div></div><div></div><div></div><div></div><div></div><div></div><div></div><div></div>
  </div>
  <svg class="abs wave" viewBox="0 0 1200 90" preserveAspectRatio="none">
    <path d="M0 40 Q300 90 600 45 T1200 35 V90 H0Z" fill="#fff"/>
    <path d="M0 40 Q300 90 600 45 T1200 35" fill="none" stroke="#1fa9d6" stroke-width="4"/>
    <path d="M0 55 Q300 100 600 60 T1200 50" fill="none" stroke="#8fd8f0" stroke-width="2"/>
  </svg>
</section>

<section class="abs intro">
  <div class="abs mark"></div>
  <h2 class="abs center serif">Bright Harbor Smile Studio</h2>
  <div class="abs center serif tag">The best price, service and results.</div>
  <p class="abs">Bright Harbor Smile Studio features state-of-the-art technologies that are safe, industry-unique and very cost-effective. Our teeth whitening system utilizes the latest blue light whitening technology. Our Blue Light Systems are calibrated precisely for optimal activation of our exclusive hydrogen-peroxide based whitening solution which is manufactured in a FDA registered facility in the USA.</p>
  <div class="abs video" role="img" aria-label="Clinic introduction video">
    <div class="abs title">Teeth Whitening Bright Harbor for $99 (Reg. $379)</div>
    <div class="abs play"></div>
    <div class="abs time">0:04 / 3:00</div>
    <div class="abs bar"></div>
  </div>
</section>

<section class="abs how">
  <h2 class="abs center serif">How It Works</h2>
  <p class="abs p1">We have a very effective teeth whitening treatment that is guaranteed to get you quick results in about 1 hour. To start the treatment you'll apply a Hydrogen Peroxide based whitening agent to your teeth. We then place our cold blue light directly in front of your exposed teeth for 15 minutes per treatment. The lighting systems we use activate the whitening agent and that's what accelerates the whitening process, giving you whiter teeth in less than an hour.</p>
  <div class="abs steps" role="img" aria-label="Six photos of the whitening treatment steps">
    <div></div><div></div><div></div><div></div><div></div><div></div>
  </div>
  <p class="abs p2">We always perform what we call a "Triple Treatment". So that's 3 of the 15 minute treatments all done consecutively, in the same visit. The actual whitening time is a total of 45 minutes. Now there is a few minute break in between each 15 minute treatment and this is why we tell all of our patients to give yourself one hour at the office. The biggest benefit of doing an in office treatment vs a take home kit is that you will see results immediately after the treatment. We also include our home maintenance kit for after care. It's very important that no matter where you get your teeth whitened, you need to maintain them for long lasting results. You'll use our maintenance kit once or twice per month as a touch up to help maintain your newly whitened teeth, and that ultimately make your results last longer.</p>
  <a class="abs btn">Book Appointment<span class="arrow">›</span></a>
</section>

<section class="abs why">
  <h2 class="abs center serif">Why Choose Us</h2>
  <div class="abs photo" role="img" aria-label="Two smiling customers holding a smile sign"></div>
  <div class="abs benefit" style="left:613px;top:203px"><div class="ring"><svg width="50" height="50" viewBox="0 0 50 50"><circle cx="25" cy="28" r="16" fill="none" stroke="#333" stroke-width="2.5"/><text x="25" y="35" text-anchor="middle" font-size="20" font-family="Montserrat" font-weight="700" fill="#333">$</text></svg></div><span>Price</span></div>
  <div class="abs benefit" style="left:794px;top:203px"><div class="ring"><svg width="50" height="50" viewBox="0 0 50 50" fill="none" stroke="#333" stroke-width="2.5"><rect x="8" y="28" width="7" height="14"/><rect x="21" y="18" width="7" height="24"/><rect x="34" y="8" width="7" height="34"/></svg></div><span>Result</span></div>
  <div class="abs benefit" style="left:975px;top:203px"><div class="ring"><svg width="50" height="50" viewBox="0 0 50 50" fill="none" stroke="#333" stroke-width="2.5"><path d="M12 10 Q25 4 38 10 Q42 22 36 40 L31 40 L28 28 L22 28 L19 40 L14 40 Q8 22 12 10Z"/></svg></div><span>No Pain</span></div>
  <div class="abs benefit" style="left:613px;top:387px"><div class="ring"><svg width="50" height="50" viewBox="0 0 50 50" fill="none" stroke="#333" stroke-width="2.5"><circle cx="25" cy="25" r="9"/><circle cx="25" cy="25" r="17" stroke-dasharray="6 5"/></svg></div><span>Services</span></div>
  <div class="abs benefit" style="left:794px;top:387px"><div class="ring"><svg width="50" height="50" viewBox="0 0 50 50" fill="none" stroke="#333" stroke-width="2.5"><path d="M38 8 L42 12 L16 38 L10 40 L12 34Z"/></svg></div><span>Convenience</span></div>
  <div class="abs benefit" style="left:975px;top:387px"><div class="ring"><svg width="50" height="50" viewBox="0 0 50 50"><circle cx="25" cy="28" r="16" fill="none" stroke="#333" stroke-width="2.5"/><text x="25" y="35" text-anchor="middle" font-size="20" font-family="Montserrat" font-weight="700" fill="#333">$</text></svg></div><span>Price</span></div>
</section>

<section class="abs compare">
  <h2 class="abs center serif">Compare Us</h2>
  <div class="abs table">
    <div class="col"><div class="head">Features</div><ul><li>Speed</li><li>Ease of Use</li><li>Cost</li><li>Availability</li><li>Pain</li></ul></div>
    <div class="col"><div class="head">Glowlamp</div><ul><li>Speed</li><li>Ease of Use</li><li>Cost</li><li>Availability</li><li>Pain</li></ul></div>
    <div class="col feature"><div class="head"><span>Bright Harbor</span><span>Smile Studio</span></div><ul><li>Speed</li><li>Ease of Use</li><li>Cost</li><li>Availability</li><li>Pain</li></ul></div>
    <div class="col"><div class="head">Pearlco</div><ul><li>Speed</li><li>Ease of Use</li><li>Cost</li><li>Availability</li><li>Pain</li></ul></div>
    <div class="col"><div class="head">Home Kits</div><ul><li>Speed</li><li>Ease of Use</li><li>Cost</li><li>Availability</li><li>Pain</li></ul></div>
  </div>
</section>

<section class="abs testi">
  <h2 class="abs center serif">What Our Client Say About</h2>
  <div class="abs chev" style="left:132px;transform:rotate(-135deg)"></div>
  <div class="abs chev" style="left:1050px;transform:rotate(45deg)"></div>
  <div class="abs card">
    <div class="abs avatar" style="top:30px" role="img" aria-label="Customer profile picture"></div>
    <div class="abs rating"><i></i><i></i><i></i><i></i><i></i></div>
    <p class="abs">My teeth look fabulous!! I've been here twice already and the staff is kind, thorough, and just plain awesome! So, with their great deal, excellent service and results--there's no excuse for you to walk around with nasty teeth. My size is coffee. I do use a straw nowadays but even with best efforts, over time, some yellowing happens. My teeth were lightened several shades my first time.</p>
    <div class="abs center who">Mara L.<br>Bright Harbor, CA</div>
  </div>
  <div class="abs center logos">
    <div class="review-mark"><span class="word">friendbook</span><span class="stars"><i></i><i></i><i></i><i></i><i></i></span></div>
    <div class="review-mark"><span class="word">rateway</span><span class="stars red"><i></i><i></i><i></i><i></i><i></i></span></div>
    <div class="review-mark"><span class="word" style="font-size:26px">searchly</span><span class="stars"><i></i><i></i><i></i><i></i><i></i></span></div>
  </div>
</section>

<footer class="abs footer">
  <div class="abs mark"></div>
  <div class="abs center addr">
    <span>● 480 Harbor View Rd, #12 | Bright Harbor, CA 90000</span>
    <span>● 1-555-014-2280</span>
  </div>
  <div class="abs links">Home &nbsp;|&nbsp; Book Appointment Online &nbsp;|&nbsp; Our Process &nbsp;|&nbsp; Photos &nbsp;|&nbsp; Testimonials &nbsp;|&nbsp; Blog &nbsp;|&nbsp; FAQ &nbsp;|&nbsp; Contact &nbsp;|&nbsp; Gift Certificates &nbsp;|&nbsp; After Care<br>Consent Form Espanol &nbsp;|&nbsp; Consent Form English &nbsp;|&nbsp; Cancellation Policy &nbsp;|&nbsp; Privacy Policy &nbsp;|&nbsp; Free Treatments</div>
  <div class="abs social"><span></span><span></span><span></span><span></span></div>
  <div class="abs center copy">©Bright Harbor Smile Studio - 2018 All Right Reserved</div>
</footer>

</body>
</html>
```